TK Stationery - Modern Contemporary

Develop modern template for Letterhead and Stationery (business card, letterhead, envelopes) using the TK Logo and Icon

Colors
0054AA
0677BA
7BADD7
CADEEF
E8F1F8
00AB8E
00BBA5
67D7C9
C6EFE9
E9F9F6
EE7325
F08F49
F5BC92
FAE3D3
FDF4ED
6B429C
8869AF
B7A5CE
E3DAEB
F3F0F8

```html
<!DOCTYPE html>
<html lang="en">
<head>
<meta charset="utf-8">
<title>TK Letterhead</title>
<link rel="stylesheet" href="https://fonts.googleapis.com/css2?family=Arimo:wght@400;700&family=Mulish:wght@700&display=swap">
<style>
  :root {
    --backdrop: #cdcccd;
    --paper: #ffffff;
    --navy: #283049;
    --green: #3db276;
    --orange: #f08a3b;
    --body-text: #555558;
    --heading-text: #4f4f52;
  }
  * { margin: 0; padding: 0; box-sizing: border-box; }
  html, body { width: 1173px; height: 1200px; overflow: hidden; background: var(--backdrop); }
  .letterhead {
    position: absolute; left: 230px; top: 96px; width: 713px; height: 1009px;
    background: var(--paper);
    font-family: "Arimo", Arial, sans-serif;
    color: var(--body-text);
  }
  .brand {
    position: absolute; left: 63px; top: 52px;
    display: flex; align-items: center; gap: 8px;
  }
  .brand-name {
    font-family: "Arimo", Arial, sans-serif; font-weight: 700;
    font-size: 36px; line-height: 1; color: var(--navy); letter-spacing: 1px;
  }
  .brand-dot { width: 8px; height: 8px; border-radius: 50%; background: var(--orange); }
  .contact { position: absolute; top: 55px; font-size: 12px; line-height: 14.5px; color: var(--navy); }
  .contact-address { right: calc(713px - 524px); text-align: right; }
  .contact-divider { position: absolute; left: 534px; top: 57px; width: 1px; height: 40px; background: var(--navy); }
  .contact-lines { left: 549px; list-style: none; }
  .contact-lines li { display: flex; align-items: center; gap: 5px; }
  .contact-lines svg { width: 9px; height: 9px; flex: none; }
  .salutation {
    position: absolute; left: 65px; top: 309px;
    font-family: "Mulish", "Century Gothic", sans-serif; font-weight: 700;
    font-size: 16.5px; color: var(--heading-text);
  }
  .letter-body { position: absolute; left: 64px; top: 357px; width: 586px; font-size: 11.6px; line-height: 14.7px; }
  .letter-body p { margin-bottom: 13px; }
  .closing {
    position: absolute; left: 65px; top: 659px;
    font-family: "Mulish", "Century Gothic", sans-serif; font-weight: 700;
    font-size: 9px; color: var(--heading-text);
  }
  .signature-area {
    position: absolute; left: 64px; top: 702px; width: 117px; height: 34px;
    background: linear-gradient(90deg, #e6e6e8, #f2f2f3);
  }
  .footer-band { position: absolute; left: 0; bottom: 0; width: 713px; height: 15px; display: block; }
</style>
</head>
<body>
  <main class="letterhead">
    <header>
      <div class="brand">
        <span class="brand-name">TK</span>
        <span class="brand-dot"></span>
      </div>
      <address class="contact contact-address" style="font-style:normal">
        Your address<br>city<br>state, ZIP 0000
      </address>
      <span class="contact-divider"></span>
      <ul class="contact contact-lines">
        <li>
          <svg viewBox="0 0 10 10"><path d="M2 1 L4 1 L4.6 3 L3.4 3.8 Q4.4 5.8 6.2 6.6 L7 5.4 L9 6 L9 8 Q8.6 9 7.5 9 Q1 8 1 2.5 Q1 1.4 2 1 Z" fill="var(--green)"/></svg>
          123-456-2100
        </li>
        <li>
          <svg viewBox="0 0 10 10"><rect x="0.5" y="2" width="9" height="6" fill="var(--green)"/><path d="M0.5 2 L5 5.5 L9.5 2" stroke="#fff" stroke-width="0.9" fill="none"/></svg>
          info@tkletters.com
        </li>
        <li>
          <svg viewBox="0 0 10 10"><circle cx="5" cy="5" r="4.5" fill="var(--green)"/><path d="M5 0.5 V9.5 M0.5 5 H9.5" stroke="#fff" stroke-width="0.7"/></svg>
          www.tkletters.com
        </li>
      </ul>
    </header>

    <h1 class="salutation">Dear Mr. Archer,</h1>

    <section class="letter-body">
      <p>Lorem ipsum dolor sit amet, consectetuer adipiscing elit, sed diam nonmmy nibh euismod tincidunt ut laor eet dolore magna aliquam erat volutpat. Ut wisi enim ad minim veniam, quis nostrud exerci tationmcorper suscipit lobortis nisl ut aliquip ex ea commodo consequat. Duis autem vel eum iriure dolor in hendrerit in vulputate velit esse molestie consequat, vel illum dolore eu feugiat</p>
      <p>Rorem ipsum dolor sit amet, consectetuer adipiscing elit, sed diam nonmmy nibh euismod tincidunt ut laor eet dolore magna aliquam erat volutpat. Ut wisi enim ad minim veniam, quis nostrud exerci tationmcorper suscipit lobortis nisl ut aliquip ex ea commodo consequat. Duis autem vel eum iriure dolor in hendrerit in vulputate velit esse molest</p>
      <p>Dorem ipsum dolor sit amet, consectetuer adipiscing elit, sed diam nonmmy nibh euismod tincidunt ut laor eet dolore magna aliquam erat volutpat. Ut wisi enim ad minim veniam, quis nostrud exerci tationmcorper suscipit lobortis nisl ut aliquip ex ea commodo consequat. Duis autem vel eum iriure dolor in hendrerit in suscipit lobortis nisl ut aliquip ex ea commodo consequat. Duis autem vel eum iriure dolor in hendrerit in vulputate velit esse molestie consequat, vel illum</p>
      <p>Sorem ipsum dolor sit amet, consectetuer adipiscing elit, sed diam nonmmy nibh euismod tincidunt ut laor eet dolore magna aliquam erat volutpat. Ut wisi enim ad minim veniam, quis nostrud exerci tationmcorper suscipit lobortis nisl ut aliquip ex ea commodo consequat. Duis autem vel eum iriure dolor in</p>
    </section>

    <p class="closing">Sincerely,</p>
    <div class="signature-area" role="img" aria-label="Handwritten signature of the sender"></div>

    <svg class="footer-band" viewBox="0 0 713 15" preserveAspectRatio="none" aria-hidden="true">
      <polygon points="0,0 518,0 506,15 0,15" fill="var(--navy)"/>
      <polygon points="528,0 713,0 713,15 516,15" fill="var(--green)"/>
    </svg>
  </main>
</body>
</html>
```